Brightfen Business Card Redesign & Logo Update

We need to update our business cards to something more modern and fresh. Brightfen can provide the current color schemes and old design examples, but welcome creativity in helping us with this redesign. PLEASE NOTE that we no longer utilize the "tree" and/or "leaf" imagery in our branding. If able would apprecaite an update on the quality of our "words only" logo in Ai. / PNG formats too.

Target Market(s)

Investors, landowners, corporate partners, contractors

Industry/Entity Type

Environmental Restoration & Conservation

Contact Information for Business Card

Logo, persons name, title, mailing address, phone and email, website url

Font styles to use
Other font styles liked:
• Merriweather

Requirements
Nice to have
• Logo, persons name, title, mailing address, phone and email, website url, but open to ideams
Should not have
• No all back backgrounds

```html
<!DOCTYPE html>
<html lang="en">
<head>
<meta charset="utf-8">
<title>Brightfen Business Card</title>
<link rel="stylesheet" href="https://fonts.googleapis.com/css2?family=Oswald:wght@700&family=Lato:wght@400;700&display=swap">
<style>
  :root {
    --backdrop: #2b2b2b;
    --card-white: #ffffff;
    --brand-green: #137a35;
    --brand-orange: #ec7a08;
    --ink-light: #ffffff;
  }
  html, body {
    margin: 0;
    padding: 0;
    width: 1200px;
    height: 1200px;
    overflow: hidden;
    background: var(--backdrop);
  }
  .canvas {
    position: relative;
    width: 1200px;
    height: 1200px;
  }
  .card {
    position: absolute;
    left: 281px;
    width: 641px;
    height: 366px;
    border-radius: 18px;
    overflow: hidden;
    box-shadow: 0 6px 18px rgba(0,0,0,0.35);
  }
  .card--front { top: 195px; background: var(--card-white); }
  .card--back  { top: 639px; background: var(--brand-orange); }

  .front-swoosh {
    position: absolute;
    inset: 0;
    width: 100%;
    height: 100%;
  }
  .swoosh-orange { fill: var(--brand-orange); }
  .swoosh-gap    { fill: var(--card-white); }
  .swoosh-green  { fill: var(--brand-green); }

  .wordmark {
    position: absolute;
    margin: 0;
    font-family: "Oswald", sans-serif;
    font-weight: 700;
    letter-spacing: 1px;
    text-transform: uppercase;
    line-height: 1;
  }
  .wordmark--front {
    left: 65px;
    top: 42px;
    font-size: 60px;
    color: var(--brand-green);
  }
  .wordmark--back {
    left: 0;
    right: 0;
    top: 118px;
    text-align: center;
    font-size: 118px;
    color: var(--ink-light);
  }

  .person {
    position: absolute;
    right: 34px;
    top: 198px;
    text-align: right;
    font-family: "Lato", sans-serif;
    color: var(--ink-light);
  }
  .person__name {
    margin: 0;
    font-size: 28px;
    font-weight: 700;
    line-height: 1.1;
    letter-spacing: 0.3px;
  }
  .person__title {
    margin: 2px 0 0;
    font-size: 18px;
    font-weight: 400;
  }

  .contact {
    position: absolute;
    top: 268px;
    font-family: "Lato", sans-serif;
    font-size: 15px;
    line-height: 23px;
    color: var(--ink-light);
    text-align: right;
    margin: 0;
    padding: 0;
    list-style: none;
  }
  .contact--address { right: 267px; }
  .contact--reach   { right: 34px; }
  .contact--reach li {
    display: flex;
    align-items: center;
    justify-content: flex-end;
    gap: 8px;
  }
  .contact-icon {
    width: 13px;
    height: 13px;
    fill: var(--ink-light);
  }
  .contact-divider {
    position: absolute;
    left: 394px;
    top: 269px;
    width: 2px;
    height: 60px;
    background: var(--ink-light);
  }
</style>
</head>
<body>
<main class="canvas">
  <section class="card card--front" aria-label="Business card front">
    <svg class="front-swoosh" viewBox="0 0 802 457" preserveAspectRatio="none" aria-hidden="true">
      <path class="swoosh-orange" d="M0,340 C150,225 350,200 555,158 C700,128 780,92 802,50 L802,457 L0,457 Z"/>
      <path class="swoosh-gap" d="M0,405 C150,275 350,232 560,186 C700,152 782,112 802,60 L802,457 L0,457 Z"/>
      <path class="swoosh-green" d="M0,414 C150,284 352,242 562,195 C702,162 786,122 802,72 L802,457 L0,457 Z"/>
    </svg>

    <h1 class="wordmark wordmark--front">Brightfen</h1>

    <div class="person">
      <p class="person__name">DANIEL HART</p>
      <p class="person__title">Founder &amp; CEO</p>
    </div>

    <ul class="contact contact--address">
      <li>123 Anywhere St</li>
      <li>Any City, State 12345</li>
      <li>www.yourwebsite.com</li>
    </ul>

    <span class="contact-divider" aria-hidden="true"></span>

    <ul class="contact contact--reach">
      <li>(123) 456-7890
        <svg class="contact-icon" viewBox="0 0 24 24" aria-hidden="true"><path d="M6.6 10.8a15.1 15.1 0 0 0 6.6 6.6l2.2-2.2a1 1 0 0 1 1-.25 11.4 11.4 0 0 0 3.6.57 1 1 0 0 1 1 1V20a1 1 0 0 1-1 1A17 17 0 0 1 3 4a1 1 0 0 1 1-1h3.5a1 1 0 0 1 1 1c0 1.25.2 2.45.57 3.6a1 1 0 0 1-.25 1z"/></svg>
      </li>
      <li>(123) 456-7890
        <svg class="contact-icon" viewBox="0 0 24 24" aria-hidden="true"><path d="M7 1h10a2 2 0 0 1 2 2v18a2 2 0 0 1-2 2H7a2 2 0 0 1-2-2V3a2 2 0 0 1 2-2zm0 3v14h10V4zm5 15.2a1.2 1.2 0 1 0 0 2.4 1.2 1.2 0 0 0 0-2.4z"/></svg>
      </li>
      <li>hello@yourwebsite.com
        <svg class="contact-icon" viewBox="0 0 24 24" aria-hidden="true"><path d="M2 5h20v14H2zm2 2v.5l8 5 8-5V7zm0 2.9V17h16V9.9l-8 5z"/></svg>
      </li>
    </ul>
  </section>

  <section class="card card--back" aria-label="Business card back">
    <h2 class="wordmark wordmark--back">Brightfen</h2>
  </section>
</main>
</body>
</html>
```